Business Card Design For A Cajun Seafood Restaurant

We are opening a cajun seafood restaurant in a week. We mainly serve cajun seafood which is orginally from Louisiana. We want design on both sides of a business card. I have menu on the website. You can go to www.reednkettle.example to check out our menu.

Restaurant name: Reed N' Kettle
Phone: +1 (555) 304-7712
Address: 48206 Ludlow Row, #7, Bexmoor Flats, Ca90000
Email: reednkettle@mailbox.example
Website: www.reednkettle.example

Maybe add social media icons (facebook, instagram) if looks nice on the business card.
facebook.com/reednkettle
instagram.com/reednkettle or @reednkettle

Attached is the logo and other business card samples that I like.

```html
<!DOCTYPE html>
<html lang="en">
<head>
<meta charset="utf-8">
<title>Reed N' Kettle – Business Card</title>
<link rel="stylesheet" href="https://fonts.googleapis.com/css2?family=Roboto:wght@400;500;700&display=swap">
<style>
  :root {
    --backdrop: #ebebea;
    --kraft: #c8a87c;
    --kraft-deep: #bf9e71;
    --ink: #221d18;
    --ink-soft: #3a322a;
    --cajun-orange: #c4511f;
    --corn-yellow: #d6a01c;
    --white: #ffffff;
  }
  * { box-sizing: border-box; margin: 0; padding: 0; }
  html, body {
    width: 1200px; height: 576px; overflow: hidden;
    background: var(--backdrop);
    font-family: "Roboto", Arial, sans-serif;
  }
  .card {
    position: absolute; top: 139px;
    width: 484px; height: 293px;
    border-radius: 7px; overflow: hidden;
    background: radial-gradient(ellipse at 40% 35%, var(--kraft) 0%, var(--kraft-deep) 100%);
  }
  .card--front { left: 82px; }
  .card--back { left: 602px; width: 481px; }

  /* Front */
  .mascot-art {
    position: absolute; left: 184px; top: 58px;
    width: 132px; height: 118px;
    border-radius: 50% 50% 42% 42%;
    background: radial-gradient(circle at 50% 55%, #d8632e 0%, #c4511f 60%, #b4481b 100%);
  }
  .front-name {
    position: absolute; left: 0; right: 0; top: 186px;
    text-align: center;
    font-weight: 700; font-size: 36px; letter-spacing: 1px;
    color: var(--ink);
  }

  /* Back */
  .holder { position: absolute; left: 26px; top: 40px; color: var(--ink); }
  .holder__name { font-size: 19px; font-weight: 500; }
  .holder__role { font-size: 11px; margin-top: 3px; color: var(--ink-soft); }
  .back-name {
    position: absolute; right: 27px; top: 40px;
    font-weight: 700; font-size: 22px; letter-spacing: 0.5px;
    color: var(--ink);
  }
  .address {
    position: absolute; left: 26px; top: 143px;
    font-size: 12px; line-height: 18px; color: var(--ink-soft);
  }
  .social { position: absolute; left: 26px; top: 184px; list-style: none; }
  .social li {
    display: flex; align-items: center; gap: 8px;
    font-size: 12px; line-height: 18px; color: var(--ink-soft);
  }
  .social__mark { width: 9px; height: 9px; background: var(--ink); border-radius: 1px; }
  .wave { position: absolute; left: 0; top: 0; }
  .contact {
    position: absolute; right: 19px; top: 216px;
    list-style: none; text-align: right;
  }
  .contact li {
    display: flex; align-items: center; justify-content: flex-end; gap: 7px;
    font-size: 12px; line-height: 18px; color: var(--white);
  }
  .contact svg { width: 10px; height: 10px; fill: var(--white); }
</style>
</head>
<body>

<section class="card card--front">
  <div class="mascot-art" role="img" aria-label="Illustrated restaurant mascot holding an ear of corn"></div>
  <div class="front-name">Reed N' Kettle</div>
</section>

<section class="card card--back">
  <svg class="wave" width="481" height="293" viewBox="0 0 481 293" aria-hidden="true">
    <path d="M0 238 C120 250 170 238 240 205 C320 168 400 142 481 126 L481 140 C400 158 330 186 250 222 C170 256 100 258 0 252 Z" fill="var(--corn-yellow)"/>
    <path d="M60 232 C150 238 210 222 290 186 C360 156 420 140 481 132 L481 136 C420 146 360 162 292 192 C212 228 150 240 60 232 Z" fill="var(--corn-yellow)" opacity="0.7"/>
    <path d="M0 258 C110 266 170 258 250 228 C330 196 400 160 481 146 L481 293 L0 293 Z" fill="var(--cajun-orange)"/>
  </svg>

  <div class="holder">
    <div class="holder__name">Jordan Hale</div>
    <div class="holder__role">Director</div>
  </div>

  <div class="back-name">Reed N' Kettle</div>

  <address class="address" style="font-style:normal">
    48206 Ludlow Row, #7,<br>Bexmoor Flats, Ca90000
  </address>

  <ul class="social">
    <li><span class="social__mark"></span>@reednkettle</li>
    <li><span class="social__mark"></span>/reednkettle</li>
  </ul>

  <ul class="contact">
    <li>+1 (555) 304-7712
      <svg viewBox="0 0 24 24"><path d="M6.6 10.8a15 15 0 0 0 6.6 6.6l2.2-2.2a1 1 0 0 1 1-.25 11.4 11.4 0 0 0 3.6.57 1 1 0 0 1 1 1V20a1 1 0 0 1-1 1A17 17 0 0 1 3 4a1 1 0 0 1 1-1h3.5a1 1 0 0 1 1 1c0 1.25.2 2.45.57 3.6a1 1 0 0 1-.25 1z"/></svg>
    </li>
    <li>www.reednkettle.example
      <svg viewBox="0 0 24 24"><path d="M2 5h20v14H2z M2 5l10 8 10-8" fill="none" stroke="#fff" stroke-width="2"/></svg>
    </li>
    <li>reednkettle@mailbox.example
      <svg viewBox="0 0 24 24"><circle cx="12" cy="12" r="9" fill="none" stroke="#fff" stroke-width="2"/><path d="M3 12h18M12 3c3 3 3 15 0 18M12 3c-3 3-3 15 0 18" fill="none" stroke="#fff" stroke-width="1.6"/></svg>
    </li>
  </ul>
</section>

</body>
</html>
```